"Outside the Box" Newsletter Design Project-Communications Company

I am looking for an Internal newsletter for a communications company that will be sent to our sales and leadership team.
This newsletter will deliver forecasting, sales results, stack rankings for the sales reps, total team results, corporate updates, success stories and updates from Training/Operations/Sales/Marketing (could be a box for each)I would also need a couple sections with a blank header and box to add info as needed, if something comes up that is not set in stone weekly.
I am looking for a template that looks sharp and professional that i can use every week by just dropping content in, (text and possibly an employee picture) I will need it in a format (possibly word) that the will keep the text in line when I drop it in each week. Once complete I can save to a pdf and would like to have the ability to drop it into the body of an email.

We have a racecar theme that we use when training our sales folks so we would like a little bit of that to the newsletter and also incorporate our color scheme from our company.

I would like four versions of the newsletter..all would match other than the title.
1. Week 1 title - Start your engines
2. Week 2 title - Looking for suggestions
3. Week 3 title - Looking for suggestions
4. Week 4 title - Approaching the finish line, this version would also include an employee spotlight, one seperate section.

If we could include a few pics around racing that would be good, not over the top, just a few to give it a little of that feel. Maybe a checkered flag with the QV logo on it, a racecar..anything else that may make sense.

I will attach our logo and our organization is called SMB (small/medium business) so that should also be placed on there somewhere. Final design would need to be two pages, sharp professional feel, my Vice President likes a very clean look, not too busy. I have also attached a sample newsletter from another group in our company, ours will not have as much content, we are much smaller but this is a sample (on a smaller scale)of what we are looking for. The company look and feel is what we want to follow. Thank you

Target Market(s)

Our Internal sales team.

Industry/Entity Type

Communications

Requirements
Must have
• Ability to update with my content without having things shift and fall out of line..format that will make that easy and then able to save to PDF..2 pages long.
Nice to have
• HTML template to match.

```html
<!DOCTYPE html>
<html lang="en">
<head>
<meta charset="utf-8">
<title>QV Weekly Newsletter – Week 1</title>
<link href="https://fonts.googleapis.com/css2?family=Open+Sans:wght@400;600;700&display=swap" rel="stylesheet">
<style>
:root{
  --page:#ebebeb;
  --card:#ffffff;
  --ink:#222222;
  --body:#555555;
  --muted:#999999;
  --rule:#e2e2e2;
  --purple:#7b3c96;
  --purple-dark:#652f7d;
  --row-alt:#f4f4f4;
  --blue:#3a87c6;
  --green:#3daa35;
  --orange:#ef8d2e;
  --yellow:#d1bd1f;
  --photo-helmet:#5e5a7a;
  --photo-person:#8a7d70;
}
*{box-sizing:border-box;margin:0;padding:0}
html,body{width:1200px;height:4152px;overflow:hidden}
body{background:var(--page);font-family:"Open Sans",Arial,sans-serif;color:var(--body);position:relative}
.wrap{position:absolute;left:112px;width:976px}
.card{background:var(--card);box-shadow:0 2px 4px rgba(0,0,0,.08)}

/* Masthead */
.masthead{top:0;height:190px;display:flex;justify-content:space-between;align-items:center}
.brand{display:flex;align-items:center;gap:18px}
.brand-mark{width:64px;height:64px;background:var(--purple);border-radius:50%}
.brand-name{font-size:58px;font-weight:700;color:var(--purple);letter-spacing:2px}
.issue{text-align:right}
.issue-date{font-size:26px;font-weight:700;color:var(--ink)}
.issue-date span{font-weight:400;color:var(--body)}
.issue-tag{font-size:20px;color:var(--body);margin-top:6px}

/* Feature */
.feature{top:200px;height:888px}
.feature-head{height:82px;display:flex;align-items:center;gap:20px;padding:0 38px}
.flag-icon{width:40px;height:40px}
.feature-title{font-size:32px;font-weight:700;color:var(--ink)}
.feature-photo{height:415px;background:linear-gradient(135deg,#8c87a8,var(--photo-helmet) 55%,#2e2b40)}
.feature-text{padding:42px 38px 0;font-size:18px;line-height:1.55}
.btn{display:inline-block;margin-top:22px;padding:12px 34px;border:2px solid #cfcfcf;border-radius:30px;font-size:18px;color:var(--ink);background:#fafafa}

/* Stories + events */
.story{left:112px;width:615px;height:260px;position:absolute;padding:24px 28px;display:flex;gap:32px}
.story-1{top:1017px}
.story-2{top:1320px;height:292px}
.date-badge{flex:0 0 88px;height:88px;background:var(--purple);color:#fff;text-align:center;padding-top:8px}
.date-badge b{display:block;font-size:34px;line-height:1.1}
.date-badge small{font-size:14px;letter-spacing:2px}
.story-title{font-size:30px;font-weight:700;color:var(--ink);margin-bottom:14px}
.story p{font-size:17px;line-height:1.6}
.events{left:760px;width:328px;top:1017px;height:595px;position:absolute;text-align:center;padding:26px 24px}
.events h3{font-size:30px;font-weight:400;color:var(--ink);margin-bottom:26px}
.event{margin-bottom:34px;font-size:19px;line-height:1.5;color:var(--body)}
.event em{font-style:normal;color:var(--purple);display:block}

/* Tables */
table{width:100%;border-collapse:collapse}
.rank{top:1648px;height:428px}
.rank th,.mtd th{background:var(--purple);color:#fff;font-size:20px;font-weight:700;text-align:left;height:83px;padding:0 36px}
.rank td{height:69px;padding:0 36px;font-size:18px;border-bottom:1px solid var(--rule)}
.rank tr:nth-child(even) td{background:var(--row-alt)}
.mtd{top:2208px;height:671px}
.mtd th{height:87px;padding:0 28px}
.mtd td{height:84px;padding:0 28px;font-size:18px}
.team td{height:62px;color:#fff;font-weight:700;font-size:18px;letter-spacing:.5px}
.team-blue td{background:var(--blue)}
.team-green td{background:var(--green)}
.team-orange td{background:var(--orange)}
.team-yellow td{background:var(--yellow)}

/* Success story */
.success{top:3018px;height:805px;padding:38px 42px}
.success h2{font-size:34px;font-weight:700;color:var(--ink);margin-bottom:16px}
.profile{display:flex;gap:34px}
.profile-photo{flex:0 0 270px;height:330px;background:linear-gradient(160deg,#b3a796,var(--photo-person) 50%,#3c3732)}
.profile h3,.record h3{font-size:26px;font-weight:700;color:var(--ink);margin-bottom:10px}
.success p{font-size:17px;line-height:1.55}
.record{margin-top:30px}
.record-body{display:flex;gap:24px}
.record-body p{flex:1}
.mini{flex:0 0 330px;font-size:11px;margin-top:10px;border:1px solid #bbb}
.mini caption{background:#1ea5dd;color:#fff;font-weight:700;padding:3px}
.mini th{background:#1ea5dd;color:#fff;font-weight:600;padding:2px 6px}
.mini td{padding:2px 6px;border-bottom:1px solid #ddd;text-align:right}
.mini td:first-child{text-align:left}

/* Footer */
.footer{top:3860px;text-align:center;font-size:15px;line-height:1.7;color:var(--muted);padding:0 40px}
.footer a{color:var(--purple)}
</style>
</head>
<body>

<header class="wrap masthead">
  <div class="brand"><div class="brand-mark"></div><div class="brand-name">QV</div></div>
  <div class="issue">
    <div class="issue-date">DECEMBER 20, 2012 <span>ISSUE</span></div>
    <div class="issue-tag">A Weekly Recap of Important Things Going on QV That You Need To Know</div>
  </div>
</header>

<section class="wrap card feature">
  <div class="feature-head">
    <svg class="flag-icon" viewBox="0 0 4 4" aria-hidden="true">
      <rect width="4" height="4" fill="#222"/>
      <rect width="1" height="1" fill="#fff"/><rect x="2" width="1" height="1" fill="#fff"/>
      <rect x="1" y="1" width="1" height="1" fill="#fff"/><rect x="3" y="1" width="1" height="1" fill="#fff"/>
      <rect y="2" width="1" height="1" fill="#fff"/><rect x="2" y="2" width="1" height="1" fill="#fff"/>
      <rect x="1" y="3" width="1" height="1" fill="#fff"/><rect x="3" y="3" width="1" height="1" fill="#fff"/>
    </svg>
    <h1 class="feature-title">WEEK 1 - Start your engines</h1>
  </div>
  <div class="feature-photo" role="img" aria-label="Close-up photo of a racing helmet on a checkered flag"></div>
  <div class="feature-text">
    <p>Far far away, behind the word mountains, far from the countries Vokalia and Consonantia, there live the blind texts. Separated they live in Bookmarksgrove right at the coast of the Semantics, a large language ocean. A small river named Duden flows by their place and supplies it with the necessary regelialia. It is a paradisematic country, in which roasted parts of sentences fly into your mouth.</p>
    <span class="btn">Read More</span>
  </div>
</section>

<article class="card story story-1">
  <div class="date-badge"><b>16</b><small>AUG</small></div>
  <div>
    <h2 class="story-title">Long Big Headline Title Here</h2>
    <p>Far far away, behind the word mountains, far from the countries Vokalia and Consonantia, there live the blind texts. Separated they live in</p>
    <span class="btn">Read More</span>
  </div>
</article>
<article class="card story story-2">
  <div class="date-badge"><b>16</b><small>AUG</small></div>
  <div>
    <h2 class="story-title">Long Big Headline Title Here</h2>
    <p>Far far away, behind the word mountains, far from the countries Vokalia and Consonantia, there live the blind texts. Separated they live in</p>
    <span class="btn">Read More</span>
  </div>
</article>

<aside class="card events">
  <h3>Upcoming Event</h3>
  <div class="event"><em>Mon, July 23</em>CR Q2 Wrap-Up Presentation @ 3 pm</div>
  <div class="event"><em>Fri, August 3</em>Double Down Mid-Year Town Hall</div>
  <div class="event"><em>June 1—August 31</em>Double Down Challenge</div>
  <div class="event"><em>June 1—August 31</em>CR TooHot To Handle Contest</div>
</aside>

<section class="wrap card rank">
  <table>
    <tr><th>Rank</th><th>Sales Rep Name</th><th>Total MTD</th><th>Total Ptc</th></tr>
    <tr><td>1</td><td>Halverson, Jon T</td><td>USD $ 50,000</td><td>90%</td></tr>
    <tr><td>2</td><td>Halverson, Jon T</td><td>USD $ 40,000</td><td>80%</td></tr>
    <tr><td>3</td><td>Marchetti, Christopher A</td><td>USD $ 38,000</td><td>70%</td></tr>
    <tr><td>4</td><td>Marchetti, Christopher A</td><td>USD $ 20,000</td><td>60%</td></tr>
    <tr><td>5</td><td>Lindqvist, Brady J</td><td>USD $ 15,000</td><td>20%</td></tr>
  </table>
</section>

<section class="wrap card mtd">
  <table>
    <tr><th>MTD Sales</th><th>MTD Ptc</th><th>July Points</th><th>June Points</th><th>Total Points</th></tr>
    <tr class="team team-blue"><td colspan="5">DENVER - TEAM CARVER</td></tr>
    <tr><td>$ 40,000</td><td>80%</td><td>1</td><td>2</td><td>3</td></tr>
    <tr class="team team-green"><td colspan="5">HOUSTON - TEAM MORETTI</td></tr>
    <tr><td>$ 40,000</td><td>80%</td><td>1</td><td>2</td><td>3</td></tr>
    <tr class="team team-orange"><td colspan="5">DALLAS - TEAM WHITLOCK</td></tr>
    <tr><td>$ 40,000</td><td>80%</td><td>1</td><td>2</td><td>3</td></tr>
    <tr class="team team-yellow"><td colspan="5">CHICAGO - TEAM ASHBY</td></tr>
    <tr><td>$ 40,000</td><td>80%</td><td>1</td><td>2</td><td>3</td></tr>
  </table>
</section>

<section class="wrap card success">
  <h2>Success Story</h2>
  <div class="profile">
    <div class="profile-photo" role="img" aria-label="Portrait photo of the featured employee"></div>
    <div>
      <h3>Say Hello For Daniel Harcourt From England.</h3>
      <p>Lorem ipsum dolor sit amet, consectetuer adipiscing elit. Aenean commodo ligula eget dolor. Aenean massa. Cum sociis natoque penatibus et magnis dis parturient montes, nascetur ridiculus mus. Donec quam felis, ultricies nec, pellentesque eu, pretium quis, sem. Nulla consequat massa quis enim. Donec pede justo, fringilla vel, aliquet nec, vulputate eget, arcu. In enim justo, rhoncus ut, imperdiet a, venenatis vitae, justo. Nullam dictum felis eu pede mollis pretium. Integer tincidunt. Cras dapibus.</p>
    </div>
  </div>
  <div class="record">
    <h3>Daniel Harcourt Record?</h3>
    <div class="record-body">
      <p>Lorem ipsum dolor sit amet, consectetuer adipiscing elit. Aenean commodo ligula eget dolor. Aenean massa. Cum sociis natoque penatibus et magnis dis parturient montes, nascetur ridiculus mus. Donec quam felis, ultricies nec, pellentesque eu, pretium quis, sem. Nulla consequat massa quis enim. Donec pede justo, fringilla vel, aliquet nec, vulputate eget, arcu. In enim justo, rhoncus ut, imperdiet a, venenatis vitae, justo. Nullam dictum felis eu pede mollis pretium. Integer tincidunt. Cras dapibus.</p>
      <table class="mini">
        <caption>CUR RANKINGS</caption>
        <tr><th>L CR</th><th>July MTD</th><th>July Ptc</th></tr>
        <tr><td>Harlow</td><td>$3,961</td><td>99%</td></tr>
        <tr><td>Crane</td><td>$3,150</td><td>87%</td></tr>
        <tr><td>Thompson</td><td>$2,602</td><td>85%</td></tr>
        <tr><td>Ellis</td><td>$2,410</td><td>80%</td></tr>
        <tr><td>Carver</td><td>$2,000</td><td>78%</td></tr>
        <tr><td>Stone</td><td>$1,870</td><td>72%</td></tr>
        <tr><td>Walton</td><td>$1,640</td><td>70%</td></tr>
        <tr><td>Moreno</td><td>$1,420</td><td>64%</td></tr>
        <tr><td>Reyes</td><td>$1,210</td><td>58%</td></tr>
      </table>
    </div>
  </div>
</section>

<footer class="wrap footer">
  <p>Sed ut perspiciatis unde omnis iste natus error sit voluptatem accusantium doloremque laudantium, totam rem aperiam, eaque ipsa quae ab illo inventore veritatis et quasi architecto beatae vitae dicta sunt explicabo. Nemo enim ipsam voluptatem quia voluptas sit aspernatur aut odit aut fugit, sed quia consequuntur magni dolores eos qui ratione voluptatem sequi nesciunt. <a>Unsubscribe Newsletter Here</a></p>
</footer>

</body>
</html>
```